Enhance Landing Page

Actual: https://thecoralparlor.com/aplique-no-litoral-lp-port/

I need a better design for this page:
Using this shortcodes : https://bolder.qrxlayouts.net
Rules:
. Keep the page header
. Keep the footer

```html
<!DOCTYPE html>
<html lang="en">
<head>
<meta charset="utf-8">
<title>The Coral Parlor — Invest in Florida</title>
<link href="https://fonts.googleapis.com/css2?family=Poppins:wght@400;500;600;700&family=Open+Sans:wght@400;600&display=swap" rel="stylesheet">
<style>
:root{
  --pink:#e0115f;
  --teal:#2a9ab0;
  --navy:#1f2650;
  --purple:#3b1a5a;
  --orange:#f26522;
  --green:#2da84a;
  --sky:#2d9cc5;
  --ink:#333;
  --muted:#666;
  --gray-bg:#ececec;
  --dark:#161616;
  --white:#fff;
}
*{box-sizing:border-box;margin:0;padding:0}
html,body{width:1200px;height:3922px;overflow:hidden}
body{position:relative;font-family:"Open Sans",Arial,sans-serif;color:var(--ink);background:var(--white)}
.abs{position:absolute}
h1,h2,h3,.brand{font-family:"Poppins",Arial,sans-serif}

/* header */
.site-header{position:absolute;left:0;top:0;width:1200px;height:118px;background:var(--white);z-index:3}
.wa-badge{left:202px;top:32px;height:24px;padding:0 12px 0 8px;background:var(--green);color:#fff;font:600 12px "Poppins",sans-serif;display:flex;align-items:center;gap:6px;border-radius:2px}
.dot{width:12px;height:12px;border-radius:50%;background:#fff;display:inline-block}
.phones{left:142px;top:66px;display:flex;gap:18px;font-size:12px;color:#333}
.phones span{display:flex;align-items:center;gap:5px}
.flag{width:16px;height:12px;display:inline-block;border-radius:2px}
.flag.br{background:var(--green)}
.flag.us{background:#3a5bb0}
.logo-cap{left:490px;top:60px;width:220px;height:108px;border-radius:0 0 110px 110px;background:var(--white);z-index:3}
.brand-header{left:490px;top:40px;width:220px;text-align:center;z-index:4}
.brand{font-weight:700;color:var(--pink);font-size:30px;letter-spacing:2px;line-height:1}
.brand small{display:block;font-size:13px;letter-spacing:5px;margin-top:6px}
.head-cta{top:40px;display:flex;align-items:center;gap:8px;font:600 11px/1.15 "Poppins",sans-serif;color:#333;text-transform:uppercase}
.head-cta .ic{width:36px;height:36px;border-radius:50%;display:flex;align-items:center;justify-content:center}
.ic.pink{background:var(--pink)}
.ic.teal{background:var(--teal)}

/* hero */
.hero{left:0;top:118px;width:1200px;height:572px;background:linear-gradient(180deg,#a9c9e4 0%,#c7dced 35%,#7fb9c4 55%,#1f8ea1 75%,#146b7d 100%)}
.hero-title{left:112px;top:448px;font:600 43px "Poppins",sans-serif;color:var(--pink)}
.hero-sub{left:112px;top:510px;font:400 25px "Poppins",sans-serif;color:var(--white);letter-spacing:.5px}
.hero-dots{left:566px;top:668px;display:flex;gap:10px}
.hero-dots i{width:9px;height:9px;border-radius:50%;border:2px solid #fff;display:block}
.hero-dots i.on{background:#fff}

/* gifts */
.gifts-title{left:112px;top:724px;font:500 26px "Poppins",sans-serif;color:var(--pink)}
.gifts-title span{color:var(--teal)}
.gifts-copy{left:112px;top:796px;width:480px;font-size:11.5px;line-height:24px;color:#444}
.gifts-copy p+p{margin-top:18px}
.btn{display:inline-block;background:var(--teal);color:#fff;font:500 14px "Poppins",sans-serif;padding:12px 30px;border-radius:3px}
.gifts-btn{left:112px;top:1028px}
.gifts-photo{left:598px;top:690px;width:602px;height:425px;background:linear-gradient(135deg,#8a6b4f,#c9b49a 45%,#e8e2d8 70%,#6f7d8c);clip-path:polygon(22% 0,100% 0,100% 100%,0 100%)}

/* welcome */
.welcome{left:0;top:1115px;width:1200px;height:857px;background:var(--gray-bg)}
.section-title{width:1200px;text-align:center;font:500 29px "Poppins",sans-serif;color:var(--pink)}
.section-title span{color:var(--teal)}
.section-lead{width:1200px;text-align:center;font-size:11.5px;color:#555}
.card{width:307px;height:256px;background:#fff;border:1px solid #d5d5d5;text-align:center;padding-top:96px}
.card h3{font:400 20px "Poppins",sans-serif;color:#222;margin-bottom:12px}
.card p{font-size:11.5px;line-height:26px;color:#666;padding:0 28px}
.badge{width:122px;height:122px;border-radius:50%;display:flex;align-items:center;justify-content:center}

/* vision */
.vision-photo{left:0;top:1972px;width:808px;height:410px;background:linear-gradient(160deg,#3f7a3a,#6fa65a 40%,#a89a7a 70%,#7a5a48)}
.vision-panel{left:808px;top:1972px;width:392px;height:410px;background:var(--teal);color:#fff;text-align:center;padding:40px 28px 0}
.vision-panel h2{font:400 36px "Poppins",sans-serif;margin-bottom:10px}
.vision-panel .lead{font:600 14px/24px "Open Sans",sans-serif;margin-bottom:20px}
.vision-panel .body{font-size:11px;line-height:26px}
.btn-outline{display:inline-block;margin-top:26px;border:2px solid #fff;border-radius:22px;padding:10px 18px;font:500 13px "Poppins",sans-serif}

/* gallery */
.tile{position:absolute}
.plus{left:324px;top:2612px;width:58px;height:58px}

/* contact */
.room-photo{left:0;top:3056px;width:563px;height:439px;background:linear-gradient(150deg,#d9d0c0,#b7a58a 45%,#7e6a55 80%,#5a4b3d)}
.need-panel{left:563px;top:3056px;width:637px;height:439px;background:var(--pink);color:#fff;padding:48px 70px}
.need-panel h2{font:400 30px "Poppins",sans-serif;margin-bottom:14px}
.need-panel .lead{font-size:14px;margin-bottom:26px}
.field{width:362px;height:38px;border:1px solid rgba(255,255,255,.85);border-radius:3px;margin-bottom:12px;font-size:11px;padding:11px 12px;color:#fff}
.field.area{height:76px}
.btn-submit{display:inline-block;margin-top:8px;background:var(--teal);color:#fff;font:500 16px "Poppins",sans-serif;padding:9px 62px 9px 60px;border-radius:3px;border:1px solid #fff}

/* footer */
.footer{left:0;top:3495px;width:1200px;height:362px;background:#f2f2f2}
.skyline{left:0;top:3525px;width:1200px;height:110px;background:linear-gradient(180deg,rgba(200,200,200,0) 0%,rgba(205,205,205,.55) 100%)}
.office{left:126px;font-size:12px;line-height:20px;color:#333}
.office h4{font:600 15px "Poppins",sans-serif;color:var(--navy);display:flex;align-items:center;gap:8px;margin-bottom:2px}
.brand-footer{left:470px;top:3680px;width:260px;text-align:center}
.brand-footer .brand{font-size:40px}
.brand-footer .brand small{font-size:16px;letter-spacing:7px}
.foot-wa{left:800px;top:3648px;width:220px;height:32px;background:var(--green);color:#fff;font:600 16px "Poppins",sans-serif;display:flex;align-items:center;justify-content:center;gap:10px;border-radius:2px}
.foot-phones{left:770px;top:3690px;display:flex;gap:16px;font-size:12.5px}
.foot-phones span{display:flex;align-items:center;gap:5px}
.foot-cta{top:3732px;display:flex;align-items:center;gap:10px;font:600 14px/1.15 "Poppins",sans-serif;color:var(--navy);text-transform:uppercase}
.foot-cta .ic{width:42px;height:42px;border-radius:50%;display:flex;align-items:center;justify-content:center}
.bottom-bar{left:0;top:3857px;width:1200px;height:65px;background:var(--dark);color:#fff;font-size:11px}
.copyright{position:absolute;left:112px;top:25px}
.foot-nav{position:absolute;right:112px;top:25px;display:flex;gap:40px;font:500 11px "Poppins",sans-serif;text-transform:uppercase}
</style>
</head>
<body>

<header class="site-header">
  <div class="abs wa-badge"><i class="dot"></i>USA +1 (555) 014-4477</div>
  <div class="abs phones">
    <span><i class="flag br"></i>+55 21 0000-4821</span>
    <span><i class="flag us"></i>+1 (555) 018-2260</span>
  </div>
  <div class="abs head-cta" style="left:786px">
    <span class="ic pink"><svg width="18" height="18" viewBox="0 0 24 24"><path d="M4 5h16v11H9l-5 4z" fill="none" stroke="#fff" stroke-width="2" stroke-linejoin="round"/></svg></span>
    <span>Fale com um<br>agente</span>
  </div>
  <div class="abs head-cta" style="left:940px">
    <span class="ic teal"><svg width="18" height="18" viewBox="0 0 24 24"><rect x="4" y="5" width="16" height="15" rx="2" fill="none" stroke="#fff" stroke-width="2"/><path d="M4 10h16M9 3v4M15 3v4" stroke="#fff" stroke-width="2"/></svg></span>
    <span>Agende uma<br>conversa</span>
  </div>
</header>
<div class="abs logo-cap"></div>
<div class="abs brand-header"><div class="brand">CORAL<small>PARLOR</small></div></div>

<section class="abs hero" role="img" aria-label="Aerial view of a Miami beach with high-rise towers, a pier and a speedboat on turquoise water"></section>
<h1 class="abs hero-title">The Coral Parlor</h1>
<p class="abs hero-sub">INVEST IN FLORIDA &amp; EFFECTIVELY TRANQUILITY</p>
<div class="abs hero-dots"><i class="on"></i><i></i><i></i></div>

<h2 class="abs gifts-title">Gifts in Brazil &amp; <span>the United States</span></h2>
<div class="abs gifts-copy">
  <p>The Coral Parlor has a permanent Lounge in Rio de Janeiro, Brazil and Orlando, Florida. With an innovative concept of 360 º assistance, advising clients who wish to buy a property in the United States, whether for Investing or Living.</p>
  <p>With the exclusive partnership of Bayline Homes, the largest construction company in the United States , we guarantee the best choices for you and your family! Our specialists have 360º vision to support you throughout the process and live the best experience in buying a property in America. Bayline Homes, the largest construction .</p>
</div>
<a class="abs btn gifts-btn">Read More</a>
<div class="abs gifts-photo" role="img" aria-label="Interior of the lounge with armchairs, wall displays and a bright window"></div>

<section class="abs welcome"></section>
<h2 class="abs section-title" style="left:0;top:1168px">Welcome to <span>The Coral Parlor</span></h2>
<p class="abs section-lead" style="left:0;top:1230px">Sed ut perspiciatis unde omnis iste natus error sit voluptatem accusantium doloremque laudantium, totam rem aperiam</p>

<div class="abs card" style="left:112px;top:1322px"><h3>Financing</h3><p>Sed ut perspiciatis unde omnis iste natus error sit voluptatem accusantium doloremque lauda ntium, totam rem aperiam</p></div>
<div class="abs card" style="left:446px;top:1322px"><h3>Financial Remittances</h3><p>Sed ut perspiciatis unde omnis iste natus error sit voluptatem accusantium doloremque lauda ntium, totam rem aperiam</p></div>
<div class="abs card" style="left:780px;top:1322px"><h3>Seen</h3><p>Sed ut perspiciatis unde omnis iste natus error sit voluptatem accusantium doloremque lauda ntium, totam rem aperiam</p></div>
<div class="abs card" style="left:112px;top:1656px"><h3>Eb-5</h3><p>Sed ut perspiciatis unde omnis iste natus error sit voluptatem accusantium doloremque lauda ntium, totam rem aperiam</p></div>
<div class="abs card" style="left:446px;top:1656px"><h3>Accounting</h3><p>Sed ut perspiciatis unde omnis iste natus error sit voluptatem accusantium doloremque lauda ntium, totam rem aperiam</p></div>
<div class="abs card" style="left:780px;top:1656px"><h3>Documentation</h3><p>Sed ut perspiciatis unde omnis iste natus error sit voluptatem accusantium doloremque lauda ntium, totam rem aperiam</p></div>

<div class="abs badge" style="left:204px;top:1282px;background:var(--pink)"><svg width="56" height="56" viewBox="0 0 56 56" fill="none" stroke="#fff" stroke-width="2.5"><rect x="8" y="12" width="40" height="26" rx="2"/><path d="M22 46h12M28 38v8"/><circle cx="28" cy="25" r="8"/><path d="M28 20v10M25 22.5h5M25 27.5h5"/></svg></div>
<div class="abs badge" style="left:538px;top:1282px;background:var(--purple)"><svg width="56" height="56" viewBox="0 0 56 56" fill="none" stroke="#fff" stroke-width="2.5"><path d="M15 8h26v40l-4-3-4 3-5-3-5 3-4-3-4 3z"/><path d="M28 16v14M24 19h6a2 2 0 010 5h-4a2 2 0 000 5h6M21 36h14"/></svg></div>
<div class="abs badge" style="left:872px;top:1282px;background:var(--orange)"><svg width="56" height="56" viewBox="0 0 56 56" fill="none" stroke="#fff" stroke-width="2.5"><rect x="10" y="14" width="30" height="30" rx="3"/><path d="M17 29l6 6 11-12"/><circle cx="42" cy="14" r="5" fill="#fff"/></svg></div>
<div class="abs badge" style="left:204px;top:1616px;background:var(--green)"><svg width="56" height="56" viewBox="0 0 56 56" fill="none" stroke="#fff" stroke-width="2.5"><rect x="14" y="10" width="28" height="38" rx="3"/><circle cx="28" cy="24" r="5"/><path d="M20 38c2-5 14-5 16 0M24 10v-4h8v4"/></svg></div>
<div class="abs badge" style="left:538px;top:1616px;background:var(--sky)"><svg width="56" height="56" viewBox="0 0 56 56" fill="none" stroke="#fff" stroke-width="2.5"><path d="M14 8h20l8 8v32H14z"/><path d="M34 8v8h8"/><rect x="20" y="24" width="16" height="18"/><path d="M20 30h16M20 36h16M28 24v18"/></svg></div>
<div class="abs badge" style="left:872px;top:1616px;background:var(--navy)"><svg width="56" height="56" viewBox="0 0 56 56" fill="none" stroke="#fff" stroke-width="2.5"><rect x="12" y="10" width="28" height="36" rx="2"/><path d="M18 18h16M18 24h16M18 30h10"/><path d="M44 14l-8 24 -2 5 4-3 8-24z"/></svg></div>

<div class="abs vision-photo" role="img" aria-label="Aerial view of a golf course with sand bunkers beside a resort community of red-roofed homes"></div>
<div class="abs vision-panel">
  <h2>360º VISION</h2>
  <p class="lead">We take care of absolutely everything to make you feel at home in Florida!</p>
  <p class="body">360º service from Brazilian to Brazilian. Our specialists will assist you in everything you need to achieve your dream of investing or living in America, with comfort and above all safety. From the choice of the best property to the opening of companies and financial remittances.</p>
  <span class="btn-outline">Do You Want To Talk Via Text Message?</span>
</div>

<h2 class="abs section-title" style="left:0;top:2424px">Do You Want To <span>Speak With A Specialist?</span></h2>
<p class="abs section-lead" style="left:0;top:2486px">Sed ut perspiciatis unde omnis iste natus error sit voluptatem accusantium doloremque laudantium, totam rem aperiam</p>

<div class="tile" style="left:112px;top:2535px;width:485px;height:217px;background:linear-gradient(135deg,#9a4f8a,#6a4f9a 50%,#3a8ab0)" role="img" aria-label="Resort entrance gate with a pink and teal overlay"></div>
<svg class="abs plus" viewBox="0 0 58 58"><circle cx="29" cy="29" r="26" fill="none" stroke="#fff" stroke-width="3"/><path d="M29 16v26M16 29h26" stroke="#fff" stroke-width="3"/></svg>
<div class="tile" style="left:112px;top:2759px;width:238px;height:219px;background:linear-gradient(180deg,#3a4a7a,#c26a4a 55%,#5a3a2a)" role="img" aria-label="Villa with a pool at dusk"></div>
<div class="tile" style="left:357px;top:2759px;width:240px;height:219px;background:linear-gradient(180deg,#2a3a6a,#b98a5a 60%,#4a3526)" role="img" aria-label="Mediterranean-style home at twilight"></div>
<div class="tile" style="left:603px;top:2535px;width:240px;height:443px;background:linear-gradient(180deg,#e9e4dc,#5a4030 40%,#a89a8a 75%,#3b2a20)" role="img" aria-label="Kitchen with dark wood cabinets and a granite island"></div>
<div class="tile" style="left:848px;top:2535px;width:238px;height:217px;background:linear-gradient(180deg,#f2f2f0,#cfd6da 60%,#b9b2a6)" role="img" aria-label="Bright dining room with a white table"></div>
<div class="tile" style="left:848px;top:2759px;width:238px;height:219px;background:linear-gradient(180deg,#d9d4cc,#4a3628 50%,#8a7a6a)" role="img" aria-label="Kitchen with dark cabinetry and bar stools"></div>

<div class="abs room-photo" role="img" aria-label="Living room with a beige sofa, wooden coffee table and patterned rug"></div>
<div class="abs need-panel">
  <h2>What You Need</h2>
  <p class="lead">Do not hesitate to speak with one of our experts.</p>
  <div class="field">Name</div>
  <div class="field">Email</div>
  <div class="field area">Message</div>
  <span class="btn-submit">Submit</span>
</div>

<footer>
  <div class="abs footer"></div>
  <div class="abs skyline" role="img" aria-label="Faint city skyline with a ferris wheel"></div>

  <div class="abs office" style="top:3648px">
    <h4><svg width="12" height="16" viewBox="0 0 12 16"><path d="M6 0a6 6 0 016 6c0 4.5-6 10-6 10S0 10.5 0 6a6 6 0 016-6z" fill="var(--pink)"/><circle cx="6" cy="6" r="2.2" fill="#fff"/></svg>Costa Verde Plaza</h4>
    <p>2nd floor next to the Food Court Av. Atlântica<br>1450, Leblon - RJ - Brazil</p>
  </div>
  <div class="abs office" style="top:3728px">
    <h4><svg width="12" height="16" viewBox="0 0 12 16"><path d="M6 0a6 6 0 016 6c0 4.5-6 10-6 10S0 10.5 0 6a6 6 0 016-6z" fill="var(--pink)"/><circle cx="6" cy="6" r="2.2" fill="#fff"/></svg>Orlando</h4>
    <p>4120 Harbor Point Drive, Suite 118, Orlando, USA</p>
  </div>
  <div class="abs office" style="top:3784px">
    <h4 style="font-size:12px"><svg width="14" height="11" viewBox="0 0 14 11"><rect width="14" height="11" rx="1.5" fill="var(--pink)"/><path d="M1 1l6 5 6-5" stroke="#fff" stroke-width="1.4" fill="none"/></svg>contact@thecoralparlor.com</h4>
  </div>

  <div class="abs brand-footer"><div class="brand">CORAL<small>PARLOR</small></div></div>

  <div class="abs foot-wa"><i class="dot" style="width:16px;height:16px"></i>USA +1 (555) 014-4477</div>
  <div class="abs foot-phones">
    <span><i class="flag br"></i>+55 21 0000-4821</span>
    <span><i class="flag us"></i>+1 (555) 018-2260</span>
  </div>
  <div class="abs foot-cta" style="left:750px">
    <span class="ic pink"><svg width="20" height="20" viewBox="0 0 24 24"><path d="M4 5h16v11H9l-5 4z" fill="none" stroke="#fff" stroke-width="2" stroke-linejoin="round"/></svg></span>
    <span>Talk to an<br>agent</span>
  </div>
  <div class="abs foot-cta" style="left:910px">
    <span class="ic teal"><svg width="20" height="20" viewBox="0 0 24 24"><rect x="4" y="5" width="16" height="15" rx="2" fill="none" stroke="#fff" stroke-width="2"/><path d="M4 10h16M9 3v4M15 3v4" stroke="#fff" stroke-width="2"/></svg></span>
    <span>Schedule a<br>conversation</span>
  </div>

  <div class="abs bottom-bar">
    <span class="copyright">© 2019 - THE CORAL PARLOR</span>
    <nav class="foot-nav"><span>Home</span><span>Properties</span><span>Magazine</span><span>Contact</span><span>Terms of use</span></nav>
  </div>
</footer>

</body>
</html>
```